Business Card front and back

I am looking for business card design. I really really like the design file I uploaded named 627788_19250069_3478263_85f427ee_image

Target Market(s)

Corporate Fitness High end Private country club

Industry/Entity Type

Fitness Industry

Contact Information for Business Card

The last image I like as an example I uploaded a bunch of my logos. The file labeled "the signature" is my business card information for you to use

Colors
0054AA
0677BA
7BADD7
CADEEF
E8F1F8

Requirements
Must have
• E-mail sigThe file I uploaded labeled "627788_19250069_3478263_85f427ee_image" with all the plus signs on the back if those could be the logo symbol I uploaded labeled "1 back.png"

```html
<!DOCTYPE html>
<html lang="en">
<head>
<meta charset="utf-8">
<title>Vantage Motion — Business Card</title>
<link href="https://fonts.googleapis.com/css2?family=Lato:wght@400;700;900&display=swap" rel="stylesheet">
<style>
  :root {
    --backdrop: #1b1b1d;
    --card: #333335;
    --brand-blue: #4a80c8;
    --ink-light: #f2f2f2;
    --ink-muted: #4a4a4d;
    --card-radius: 28px;
  }
  * { box-sizing: border-box; margin: 0; padding: 0; }
  html, body {
    width: 1200px; height: 1122px; overflow: hidden;
    background: var(--backdrop);
    font-family: "Lato", sans-serif;
  }
  .sheet {
    width: 1200px; height: 1122px;
    display: flex; flex-direction: column; align-items: center; justify-content: center;
    gap: 60px;
  }
  .card {
    width: 760px; height: 434px;
    background: var(--card);
    border-radius: var(--card-radius);
    position: relative;
    overflow: hidden;
  }

  /* Front */
  .card-front { display: flex; align-items: center; justify-content: center; }
  .brand-lockup { display: flex; align-items: center; gap: 22px; }
  .brand-square { width: 46px; height: 46px; background: var(--brand-blue); flex: none; }
  .brand-name {
    font-weight: 900; font-size: 54px; letter-spacing: 3px;
    color: var(--brand-blue); text-transform: uppercase; white-space: nowrap;
  }

  /* Back */
  .card-back { display: flex; align-items: center; }
  .back-mark {
    width: 330px; padding-left: 48px;
    font-weight: 900; font-size: 50px; line-height: 1.05; letter-spacing: 2px;
    color: var(--ink-muted); text-transform: uppercase;
  }
  .contact-block { flex: 1; padding-right: 50px; }
  .person-name {
    font-weight: 900; font-size: 40px; color: var(--brand-blue);
    letter-spacing: 1px; text-transform: uppercase; white-space: nowrap;
  }
  .person-role { font-size: 22px; color: var(--ink-light); margin-top: 2px; }
  .divider { height: 2px; background: var(--brand-blue); margin: 16px 0 20px; }
  .contact-list { list-style: none; display: flex; flex-direction: column; gap: 8px; }
  .contact-item {
    display: flex; align-items: center; gap: 14px;
    font-size: 20px; color: var(--ink-light); white-space: nowrap;
  }
  .contact-item.phone { font-weight: 900; font-size: 23px; }
  .contact-icon { width: 18px; height: 18px; flex: none; fill: var(--brand-blue); }
</style>
</head>
<body>
<main class="sheet">
  <section class="card card-front" aria-label="Card front">
    <div class="brand-lockup">
      <span class="brand-square"></span>
      <span class="brand-name">Vantage Motion</span>
    </div>
  </section>

  <section class="card card-back" aria-label="Card back">
    <div class="back-mark">Vantage<br>Motion</div>
    <div class="contact-block">
      <h1 class="person-name">Daniel Reyes</h1>
      <p class="person-role">Consultant</p>
      <div class="divider"></div>
      <ul class="contact-list">
        <li class="contact-item phone">
          <svg class="contact-icon" viewBox="0 0 24 24"><path d="M6.6 10.8a15 15 0 0 0 6.6 6.6l2.2-2.2a1 1 0 0 1 1-.25 11.4 11.4 0 0 0 3.6.6 1 1 0 0 1 1 1V20a1 1 0 0 1-1 1A17 17 0 0 1 3 4a1 1 0 0 1 1-1h3.5a1 1 0 0 1 1 1c0 1.25.2 2.45.6 3.6a1 1 0 0 1-.25 1z"/></svg>
          555-014-7720
        </li>
        <li class="contact-item">
          <svg class="contact-icon" viewBox="0 0 24 24"><path d="M2 5h20v14H2z M3.5 6.5 12 13l8.5-6.5" /></svg>
          dan@vantagemotion.co
        </li>
        <li class="contact-item">
          <svg class="contact-icon" viewBox="0 0 24 24"><circle cx="12" cy="12" r="10"/></svg>
          vantagemotion.co
        </li>
        <li class="contact-item">
          <svg class="contact-icon" viewBox="0 0 24 24"><path d="M12 2a7 7 0 0 0-7 7c0 5.2 7 13 7 13s7-7.8 7-13a7 7 0 0 0-7-7zm0 9.5A2.5 2.5 0 1 1 12 6.5a2.5 2.5 0 0 1 0 5z"/></svg>
          NV. AZ. NM. CO. UT. WY
        </li>
      </ul>
    </div>
  </section>
</main>
</body>
</html>
```